Velmora Systems Website

Website design for our company: Velmora Systems.
The website should look fresh and IT focused. Please have a look at http://www.velmorasystems.example.au/ for our current design. We want something fresh and new, professional looking, in WordPress so we can easily make changes.

It Company

```html
<!DOCTYPE html>
<html lang="en">
<head>
<meta charset="utf-8">
<title>Velmora Systems</title>
<link href="https://fonts.googleapis.com/css2?family=Open+Sans:wght@300;400;600;700&display=swap" rel="stylesheet">
<style>
:root{
  --blue:#0b63c1;
  --blue-dark:#0a2a6a;
  --green:#00b050;
  --ink:#3a3d42;
  --text:#4a4d52;
  --panel:#f2f2f2;
  --panel-2:#e6e6e6;
  --footer:#45464b;
  --footer-text:#c9cacd;
  --white:#ffffff;
}
*{box-sizing:border-box;margin:0;padding:0}
html,body{width:1024px;height:1200px;overflow:hidden}
body{font-family:"Open Sans",Arial,sans-serif;color:var(--text);background:var(--panel);position:relative}
.abs{position:absolute}

.topline{left:0;top:0;width:1024px;height:3px;background:var(--blue)}
.header{left:0;top:3px;width:1024px;height:76px;background:#f5f5f5}
.brand{left:137px;top:9px;height:56px;display:flex;align-items:center;gap:10px;font-weight:700;font-size:20px;color:var(--green);white-space:nowrap}
.brand-mark{flex:none;width:34px;height:34px;background:var(--green);border-radius:4px}

.remote{left:632px;top:0;width:264px;height:41px;background:var(--blue);border-radius:0 0 6px 6px}
.remote-label{left:15px;top:7px;color:var(--white);font-weight:700;font-size:11px;line-height:13px}
.remote-field{left:80px;top:7px;width:176px;height:27px;background:#3d4045;border-radius:3px}
.remote-field span{position:absolute;left:8px;top:8px;font-size:8px;color:#c8c9cc;white-space:nowrap}
.btn-dark{position:absolute;right:2px;top:2px;height:23px;width:54px;background:#55585d;border-radius:3px;font-size:8px;color:#e0e0e0;display:flex;align-items:center;justify-content:center}

.nav{left:0;top:79px;width:1024px;height:35px;background:linear-gradient(#3bc56f,#14ad52);border-top:1px solid #7fd9a1}
.nav a{position:absolute;top:11px;color:var(--white);font-weight:700;font-size:11.5px;text-decoration:none}
.search{left:712px;top:3px;width:176px;height:27px;background:#f0f1f2;border-radius:3px}
.search span{position:absolute;left:8px;top:7px;font-size:10.5px;color:#9a9da1}
.search svg{position:absolute;right:8px;top:6px}

.hero{left:0;top:114px;width:1024px;height:323px;background:radial-gradient(ellipse at 50% 40%,#d6e8f8 0%,#6fa8dc 30%,#1f4f9a 60%,var(--blue-dark) 100%)}
.arrow{width:38px;height:38px;border-radius:50%;background:#2b63b4;border:2px solid #4a7bc4;display:flex;align-items:center;justify-content:center}

.tagline{left:0;top:437px;width:1024px;height:84px;background:linear-gradient(90deg,#2fbf68,#45cb80 40%,var(--green))}
.tagline h1{position:absolute;left:137px;top:18px;font-weight:300;font-size:24px;color:var(--white);white-space:nowrap}
.tagline p{position:absolute;left:141px;top:47px;font-size:14px;color:var(--white);white-space:nowrap}

.services{left:0;top:521px;width:1024px;height:241px;background:var(--panel)}
.section-title{font-weight:300;font-size:20px;color:#4a4d52;white-space:nowrap}
.services .section-title{left:0;width:1000px;top:26px;text-align:center}
.rule{left:136px;top:67px;width:752px;height:2px;background:#d5d6d8}
.notch{left:507px;top:68px;width:0;height:0;border-left:5px solid transparent;border-right:5px solid transparent;border-top:5px solid #d5d6d8}
.service{display:flex;align-items:center;gap:10px;font-weight:700;font-size:11.5px;color:var(--ink);line-height:16px;white-space:nowrap}
.service i{flex:none;width:32px;height:32px;border-radius:50%;background:var(--ink);display:flex;align-items:center;justify-content:center}
.service.active{color:var(--blue)}
.service.active i{background:#dbe8f6;border:2px solid #3a86d6}

.about{left:0;top:762px;width:1024px;height:207px;background:var(--panel-2)}
.avatar{border-radius:50%;border:3px solid #fafafa;box-shadow:0 0 0 1px #c8c9cb;background:radial-gradient(circle at 50% 40%,#b9bbbe,#6d7074)}
.about-text{left:219px;top:58px;width:255px;font-size:10.5px;line-height:16px}
.btn-light{left:219px;top:150px;width:82px;height:27px;background:#f5f5f5;border:1px solid #d2d3d5;border-radius:3px;font-size:8px;color:#555;display:flex;align-items:center;justify-content:center}
.person{left:521px;top:129px;font-size:8px;line-height:10px;white-space:nowrap;z-index:2}
.person b{display:block;font-size:8.5px;color:var(--ink)}
.quote{left:612px;top:69px;width:276px;height:104px;background:#8e9297;border-radius:3px;border-bottom:3px solid #b4b6b9}
.quote-tail{left:594px;top:86px;width:0;height:0;border-top:11px solid transparent;border-bottom:11px solid transparent;border-right:18px solid #8e9297}
.quote p{position:absolute;left:25px;top:25px;width:235px;font-size:10.5px;line-height:16px;color:var(--white)}
.quote .mark{position:absolute;right:14px;top:-14px;font-size:110px;font-weight:700;color:#82868b;line-height:110px}

.footer{left:0;top:969px;width:1024px;height:216px;background:var(--footer);color:var(--footer-text)}
.footer-brand{left:138px;top:36px;height:74px;display:flex;align-items:center;gap:9px;font-weight:700;font-size:16px;color:var(--white);white-space:nowrap}
.footer-brand .brand-mark{width:28px;height:28px}
.copy{left:137px;top:168px;font-size:9.5px;color:#7c7e83;white-space:nowrap}
.footer h3{position:absolute;font-size:11.5px;font-weight:700;color:#d8d9db;white-space:nowrap}
.footer ul{position:absolute;list-style:none;font-size:10.5px;line-height:16px}
.footer li::before{content:"";display:inline-block;border-left:4px solid #c9cacd;border-top:3px solid transparent;border-bottom:3px solid transparent;margin-right:6px}
.contact{font-size:10.5px;line-height:16px;white-space:nowrap}
.footer-field{left:713px;top:90px;width:175px;height:27px;background:#3b3c40;border-radius:3px;box-shadow:inset 0 1px 2px #2c2d30}
.social{left:713px;top:164px;display:flex;gap:14px}
.social span{width:14px;height:14px;border-radius:50%;background:#6d6f74}
.bottom{left:0;top:1185px;width:1024px;height:15px;background:var(--green)}
</style>
</head>
<body>
<div class="abs topline"></div>
<header class="abs header">
  <div class="abs brand"><span class="brand-mark"></span>Velmora Systems</div>
</header>
<div class="abs remote">
  <div class="abs remote-label">REMOTE<br>SUPPORT</div>
  <div class="abs remote-field"><span>ENTER -6 DIGIT CODE</span><div class="btn-dark">CONNECT</div></div>
</div>

<nav class="abs nav">
  <a style="left:152px">HOME</a>
  <a style="left:244px">SERVICES</a>
  <a style="left:356px">PORTFOLIO</a>
  <a style="left:478px">ABOUT</a>
  <a style="left:581px">CONTACTS</a>
  <div class="abs search"><span>Search the site</span>
    <svg width="15" height="15" viewBox="0 0 15 15"><circle cx="9" cy="6" r="4.5" fill="none" stroke="#555" stroke-width="1.3"/><line x1="5.8" y1="9.2" x2="1.5" y2="13.5" stroke="#555" stroke-width="1.5"/></svg>
  </div>
</nav>

<section class="abs hero" role="img" aria-label="Team of business people in suits standing in front of a globe">
  <div class="abs arrow" style="left:89px;top:145px"><svg width="8" height="8" viewBox="0 0 8 8"><path d="M5 1 2 4l3 3" fill="none" stroke="#fff" stroke-width="1.4"/></svg></div>
  <div class="abs arrow" style="left:894px;top:145px"><svg width="8" height="8" viewBox="0 0 8 8"><path d="M3 1l3 3-3 3" fill="none" stroke="#fff" stroke-width="1.4"/></svg></div>
</section>

<section class="abs tagline">
  <h1>Velmora Systems is an Adelaide based company with a single objective</h1>
  <p>- to excel in the support and service of all computer and IT needs.</p>
</section>

<section class="abs services">
  <h2 class="abs section-title">OUR SERVICES</h2>
  <div class="abs rule"></div><div class="abs notch"></div>
  <div class="abs service active" style="left:137px;top:96px"><i><svg width="12" height="10"><rect x="0" y="0" width="12" height="8" rx="3" fill="#3a86d6"/></svg></i>ON-SITE SERVICE</div>
  <div class="abs service" style="left:329px;top:96px"><i><svg width="14" height="14"><rect x="3" y="3" width="8" height="8" fill="none" stroke="#fff" stroke-width="1.5"/></svg></i>MEDICAL IT SERVICE</div>
  <div class="abs service" style="left:521px;top:96px"><i><svg width="16" height="16"><circle cx="8" cy="8" r="6" fill="none" stroke="#fff" stroke-width="1.5"/></svg></i>REMOTE DESKTOP</div>
  <div class="abs service" style="left:713px;top:96px"><i><svg width="14" height="14"><path d="M7 2 12 12H2z" fill="#fff"/></svg></i>PHARMACY IT SERVICE</div>
  <div class="abs service" style="left:137px;top:154px"><i><svg width="12" height="14"><rect x="1" y="1" width="10" height="12" fill="none" stroke="#fff" stroke-width="1.4"/></svg></i>HARDWARE/ SOFTWARE<br>SUPPLY</div>
  <div class="abs service" style="left:329px;top:154px"><i><svg width="14" height="14"><path d="M12 1 4 10 3 13 6 12 13 2z" fill="#fff"/></svg></i>WEBSITE DESIGN</div>
  <div class="abs service" style="left:521px;top:154px"><i><svg width="14" height="14"><path d="M7 1 13 7 7 13 1 7z" fill="none" stroke="#fff" stroke-width="1.6"/></svg></i>DISASTER RECOVERY</div>
  <div class="abs service" style="left:713px;top:154px"><i><svg width="14" height="14"><g stroke="#fff" stroke-width="1.5"><line x1="2" y1="1" x2="2" y2="13"/><line x1="5.5" y1="1" x2="5.5" y2="13"/><line x1="9" y1="1" x2="9" y2="13"/><line x1="12.5" y1="1" x2="12.5" y2="13"/></g></svg></i>CONSUMABLES</div>
</section>

<section class="abs about">
  <h2 class="abs section-title" style="left:138px;top:26px">WELCOME TO OUR SITE!</h2>
  <div class="abs avatar" role="img" aria-label="Portrait photo of a smiling man" style="left:138px;top:67px;width:68px;height:68px"></div>
  <p class="abs about-text">Because we know you don't want to be limited on a portrait or scape format we made Showcase. compatible in both portrait AND landscape! Yes, we care about you.</p>
  <div class="abs btn-light">READ MORE</div>

  <h2 class="abs section-title" style="left:521px;top:26px">WHAT PEOPLE SAY</h2>
  <div class="abs avatar" role="img" aria-label="Portrait photo of a smiling woman" style="left:522px;top:67px;width:52px;height:52px"></div>
  <div class="abs quote-tail"></div>
  <div class="abs quote"><span class="mark">&ldquo;</span><p>Because we know you don't want to be limited on a portrait or scape format we made Showcase. compatible in both portrait AND landscape!</p></div>
  <div class="abs person"><b>MARA LINDQVIST</b>CEO, LINDQVIST CO</div>
</section>

<footer class="abs footer">
  <div class="abs footer-brand"><span class="brand-mark"></span>Velmora Systems</div>
  <div class="abs copy">&copy; 2014 Velmora Systems. All Rights Reserved</div>

  <h3 style="left:365px;top:36px">NAVIGATION</h3>
  <ul style="left:365px;top:64px">
    <li>HOME</li><li>CLIENTS</li><li>SERVICES</li><li>SUPPORTS</li><li>TESTIMONIALS</li><li>CONTACT US</li><li>ABOUT US</li>
  </ul>

  <h3 style="left:521px;top:36px">CONTACTS</h3>
  <div class="abs contact" style="left:521px;top:64px">Northgate Pty Ltd<br>PO Box 40512<br>Harlow Lane, Melbourne<br>Victoria 3999 Australia<br><br>Phone: (08) 5550 0147<br>support@velmora.example.au</div>

  <h3 style="left:713px;top:36px">REMOTE SUPPORT</h3>
  <div class="abs contact" style="left:713px;top:64px">Enter you 6-digit code</div>
  <div class="abs footer-field"><div class="btn-dark">CONNECT</div></div>
  <h3 style="left:713px;top:136px">GET SOCIAL</h3>
  <div class="abs social"><span></span><span></span><span></span><span></span><span></span></div>
</footer>
<div class="abs bottom"></div>
</body>
</html>
```